Emerging automotive detailing business

I am starting a small automotive detailing business in hopes of becoming a well-known detailer to work on high end cars. I would like a card to reflect the high quality and time I put into my work. The name of the company is Bright Crest Detailing. I feel like it represents racecars getting off the line at the drag strip as well as an innuendo of "Up the Ladder". I do minor paint correction such as clay barring, multi-step buffing and polishing, waxing, hand washes, etc. I am always striving to learn more and improve my work. My goal is to have total customer satisfaction. This is a female run business but I do not want it to be very girly. Elegant is okay! I have pictures of my personal wrenfield attached, they do not need to be incorporated but if you can think of a cool way to use 1 or all of them, go for it!

Target Market(s)

Anyone that owns a vehicle. Preferably high end vehicles such as Valtori, Castellverde and Morvani but I will also happily work on any car, truck or suv no matter what brand.

Industry/Entity Type

Automotive

Contact Information for Business Card

Bright Crest Detailing
Mira Tolland
4175 Quenhollow Rd
Ashmere PA 17492
Cell phone- call/text- 717-555-0148
email- brightcrestdetails@maildrop-example.com
Instagram: @brightcrestdetailing
Facebook: facebook.com/brightcrestdetailing

Requirements
Must have
• Business name, my name, address, phone number. Listing that I do minor paint correction such as clay barring, multi-step buffing and polishing, waxing, hand washes, interior cleaning, and more. (This last part was in nice to haves but I have realized that I do really want it, so I moved it to must haves.) I want something that is different and eye-catching to my customers. Some people have done this very well with cards already submitted to me, but a lot have not. I didn't mess with the "look and feel bars" much because because I am pretty open to the overall design as long as it is not your basic run of the mill design.
Nice to have
• Something car related. Maybe an appointment time/date line. I do not have a logo, but if you would like to design one and incorporate it, that would be amazing!
Should not have
• Purple and Pink colors. Boring, basic, normal card.

```html
<!DOCTYPE html>
<html lang="en">
<head>
<meta charset="utf-8">
<title>Bright Crest Detailing – Business Card</title>
<link href="https://fonts.googleapis.com/css2?family=Open+Sans:wght@400;600;700&display=swap" rel="stylesheet">
<style>
  :root {
    --bg: #d9d9d6;
    --card-dark: #0b0c0f;
    --card-light-top: #ffffff;
    --card-light-bottom: #e6e6e6;
    --accent-red: #e1252b;
    --accent-blue: #1f8fd6;
    --text-light: #f2f2f2;
    --icon-blue: #3aa7e0;
  }
  * { margin: 0; padding: 0; box-sizing: border-box; }
  html, body {
    width: 1200px; height: 1000px; overflow: hidden;
    background: var(--bg);
    font-family: "Open Sans", Arial, sans-serif;
  }
  .card {
    position: absolute;
    width: 727px; height: 437px;
    overflow: hidden;
    box-shadow: 0 6px 18px rgba(0,0,0,0.25);
  }
  .card-front {
    left: 55px; top: 44px;
    background: linear-gradient(var(--card-light-top), var(--card-light-bottom) 60%);
  }
  .card-back {
    left: 395px; top: 508px;
    background: var(--card-dark);
  }
  .front-wave { position: absolute; left: 0; top: 0; width: 727px; height: 437px; }
  .brand-mark {
    position: absolute; left: 50%;
    border: 3px solid var(--accent-blue);
    border-radius: 50%;
    transform: translateX(-50%);
  }
  .card-front .brand-mark { top: 38px; width: 96px; height: 96px; }
  .card-back .brand-mark { top: 56px; width: 124px; height: 124px; }
  .brand-name {
    position: absolute; left: 0; right: 0;
    text-align: center;
    font-weight: 700; font-size: 27px; letter-spacing: 0.5px;
    color: var(--accent-red);
    text-transform: uppercase;
  }
  .card-front .brand-name { top: 146px; }
  .card-back .brand-name { top: 194px; font-size: 30px; }
  .owner-name {
    position: absolute; left: 0; width: 730px; top: 240px;
    text-align: center;
    font-weight: 600; font-size: 25px;
    color: var(--accent-red);
  }
  .contact-line {
    position: absolute;
    display: flex; align-items: center; gap: 10px;
    color: var(--text-light); font-size: 20px;
  }
  .contact-line svg { width: 22px; height: 22px; flex: none; }
  .contact-phone { left: 48px; top: 343px; }
  .contact-email { left: 48px; top: 377px; font-size: 17px; }
  .contact-address {
    position: absolute; left: 464px; top: 345px;
    display: flex; gap: 8px;
    color: var(--text-light); font-size: 21px; line-height: 28px;
  }
  .contact-address svg { width: 22px; height: 22px; margin-top: 2px; flex: none; }
  .contact-address address { font-style: normal; }
  .services {
    position: absolute; left: 0; right: 0; top: 283px;
    text-align: center;
    color: #ffffff; font-weight: 700; font-size: 17.5px; line-height: 27px;
    text-transform: uppercase;
  }
  .services .dot { color: var(--accent-red); padding: 0 5px; }
  .social-handle {
    position: absolute; left: 0; right: 0; top: 374px;
    display: flex; justify-content: center; align-items: center; gap: 9px;
    color: var(--text-light); font-size: 19px;
  }
  .social-square {
    width: 25px; height: 25px; border-radius: 3px;
    background: var(--icon-blue);
  }
</style>
</head>
<body>

<section class="card card-front">
  <svg class="front-wave" viewBox="0 0 727 437" aria-hidden="true">
    <path d="M0,253 Q363,149 727,253 L727,437 L0,437 Z" fill="var(--card-dark)"/>
    <path d="M0,253 Q363,149 727,253" fill="none" stroke="var(--accent-blue)" stroke-width="5"/>
  </svg>
  <span class="brand-mark" aria-hidden="true"></span>
  <div class="brand-name">Bright Crest Detailing</div>
  <div class="owner-name">Mira Tolland</div>

  <div class="contact-line contact-phone">
    <svg viewBox="0 0 24 24" aria-hidden="true">
      <circle cx="12" cy="12" r="10.5" fill="none" stroke="var(--icon-blue)" stroke-width="1.6"/>
      <path d="M9 7.2c.4-.4 1-.4 1.3 0l1 1.4c.3.4.2.9-.1 1.2l-.6.5c.5 1.2 1.4 2.1 2.6 2.6l.5-.6c.3-.3.8-.4 1.2-.1l1.4 1c.4.3.4.9 0 1.3l-.8.8c-.6.6-1.6.7-2.4.3-2.2-1.1-3.9-2.8-5-5-.4-.8-.3-1.8.3-2.4z" fill="var(--icon-blue)"/>
    </svg>
    <span>717-555-0148</span>
  </div>
  <div class="contact-line contact-email">
    <svg viewBox="0 0 24 24" aria-hidden="true">
      <rect x="2" y="5" width="20" height="14" rx="1.5" fill="none" stroke="var(--icon-blue)" stroke-width="1.7"/>
      <path d="M2.5 6l9.5 7 9.5-7" fill="none" stroke="var(--icon-blue)" stroke-width="1.7"/>
    </svg>
    <span>brightcrestdetails@maildrop-example.com</span>
  </div>
  <div class="contact-address">
    <svg viewBox="0 0 24 24" aria-hidden="true">
      <path d="M12 3L2 12h3v9h5v-6h4v6h5v-9h3z" fill="var(--icon-blue)"/>
    </svg>
    <address>4175 Quenhollow Rd<br>Ashmere PA 17492</address>
  </div>
</section>

<section class="card card-back">
  <span class="brand-mark" aria-hidden="true"></span>
  <div class="brand-name">Bright Crest Detailing</div>
  <p class="services">
    Clay Barring<span class="dot">•</span>Multi-Step Buffing and Polishing<br>
    Waxing<span class="dot">•</span>Hand Washes<span class="dot">•</span>Interior Cleaning and More
  </p>
  <div class="social-handle">
    <span class="social-square" aria-hidden="true"></span>
    <span>@brightcrestdetailing</span>
  </div>
</section>

</body>
</html>
```